Bluefinch Painting needs a Website

We need a website built for a Painting company I own, we mainly do residential painting, but don't want to be limited to that.

Need to have estimate request form.
Need pic's of past projects

I like the look of the website for http://www.harbor-brushworks.com
& "Westlake Home inspections"

My logo that was designed here on ArtHatch on the front page

I would like one of the houses I downloaded as part of the background
of the front page.

Target Market(s)

Home owners

Industry/Entity Type

Painting

Number of Pages Required

1 page

Font styles to use
Serif

Requirements
Must have
• Estimate request form for home owners to fill out -
• Name:
• Phone Number:
• Address:
• E-mail:
• Painting project description:
• And my info to:
• My phone number: (555) 318-7046
• My web address bluefinchpainting.example
Nice to have
• My logo that was designed here on ArtHatch

```html
<!DOCTYPE html>
<html lang="en">
<head>
<meta charset="utf-8">
<title>Bluefinch Painting</title>
<link rel="stylesheet" href="https://fonts.googleapis.com/css2?family=Arimo:wght@400;700&family=Roboto+Slab:wght@400&family=Tinos:wght@400;700&family=PT+Serif:wght@400;700&display=swap">
<style>
:root{
  --blue:#1f7fc4;
  --blue-dark:#176aa8;
  --ink:#111;
  --text:#333;
  --panel:#e7f0f7;
  --side:#e2edf6;
  --field:#f2f6fa;
  --black:#000;
  --white:#fff;
  --hero-a:#e3b53a;
  --hero-b:#c99a2a;
}
*{box-sizing:border-box;margin:0;padding:0}
html,body{width:1034px;height:1200px;overflow:hidden;background:var(--white)}
body{position:relative;font-family:"Tinos",serif;color:var(--text)}
.abs{position:absolute}

/* header */
.brand{left:138px;top:30px;display:flex;align-items:center;gap:10px}
.brand-square{width:34px;height:34px;background:var(--blue)}
.brand-name{font-family:"Tinos",serif;font-size:31px;color:var(--ink);letter-spacing:1px}
.truck-photo{left:558px;top:20px;width:170px;height:84px;background:linear-gradient(#f3f3f3,#cfd3d8);border-radius:4px}
.estimate-btn{left:756px;top:20px;width:129px;height:25px;background:var(--blue);color:var(--white);font-family:"Arimo",sans-serif;font-size:15px;text-align:center;line-height:25px}
.call{left:760px;top:60px;display:flex;align-items:center;gap:7px;font-family:"Arimo",sans-serif;color:#222}
.call small{display:block;font-size:12px}
.call strong{display:block;font-size:17px;font-weight:400}

/* nav */
.nav{left:0;top:104px;width:1034px;height:34px;background:var(--blue);font-family:"Roboto Slab",serif;font-size:13.5px}
.nav ul{list-style:none;position:absolute;left:139px;top:0;display:flex;height:34px}
.nav li{color:var(--white);line-height:34px;padding:0 20px;border-right:1px solid var(--blue-dark)}
.nav li.current{background:var(--black);padding:0 11px}

/* hero */
.hero{left:0;top:138px;width:1034px;height:268px;background:linear-gradient(100deg,#e6e3da 0%,#c9b98d 35%,var(--hero-a) 60%,var(--hero-b) 100%)}
.hero-arrow{top:113px;width:36px;height:36px;border-radius:50%;background:#222;box-shadow:0 0 0 4px rgba(0,0,0,.25)}
.hero-tag{right:157px;top:100px;text-align:right;font-family:"Roboto Slab",serif;font-size:20px;line-height:27px;color:#111}
.hero-tag em{font-style:normal;color:#1c4f9a}

/* about */
.about{left:138px;top:406px;width:495px;height:247px;background:var(--panel)}
.about h2{position:absolute;left:20px;top:18px;font-weight:400;font-size:20px;color:var(--ink)}
.about h2 span,.section-title span{color:var(--blue)}
.about p{position:absolute;left:20px;top:53px;width:445px;font-size:11.3px;line-height:17.2px}
.btn{display:inline-block;background:var(--black);color:var(--white);font-family:"Tinos",serif;font-weight:700;font-size:10px;border-radius:2px;text-align:center}
.about .btn{position:absolute;left:18px;top:164px;width:68px;height:22px;line-height:22px}
.quality{position:absolute;left:16px;top:207px;font-family:"Roboto Slab",serif;font-size:15px;color:#333}
.paint-brand{position:absolute;left:216px;top:209px;font-family:"Tinos",serif;font-size:15px;color:#2a4a8a}

/* services */
.service{top:670px;width:250px}
.service h3{font-weight:400;font-size:18px;color:var(--ink)}
.service .photo{margin-top:12px;width:230px;height:146px;border:3px solid #ddd}
.service p{margin-top:8px;margin-left:2px;font-size:10.5px;line-height:16px;width:205px}
.rule{height:1px;background:#ccc}
.service .btn,.gallery-nav{position:absolute}
.service .rule{position:absolute;left:0;top:261px;width:213px}
.service .btn{left:73px;top:251px;width:68px;height:22px;line-height:22px}

/* side */
.side{left:646px;top:406px;width:251px;height:574px;background:var(--side)}
.section-title{position:absolute;font-family:"PT Serif",serif;font-size:18.5px;color:var(--blue)}
.form{position:absolute;left:11px;top:56px;width:183px}
.field{display:block;width:183px;height:26px;margin-bottom:9px;background:var(--field);font-family:"Arimo",sans-serif;font-size:11px;color:#333;padding:6px 9px}
.field.area{height:62px}
.side .rule{position:absolute;left:11px;width:212px}
.submit{position:absolute;left:91px;top:271px;width:55px;height:23px;background:var(--black);color:var(--white);font-family:"Arimo",sans-serif;font-weight:700;font-size:12px;line-height:23px;text-align:center;border-radius:2px}
.gallery-mark{position:absolute;left:47px;top:312px;width:30px;height:30px;background:var(--blue)}
.gallery-photo{position:absolute;left:11px;top:358px;width:230px;height:146px;border:3px solid #ddd;background:linear-gradient(90deg,#ece9e1,#f6f5f0 70%,#1a2340 72%)}
.gallery-caption{position:absolute;left:0;bottom:0;width:100%;height:28px;background:rgba(0,0,0,.45);color:var(--white);font-size:15px;line-height:28px;padding-left:6px}
.gallery-nav{left:109px;top:522px;display:flex;gap:2px}
.gallery-nav span{width:15px;height:14px;background:var(--black)}

/* footer */
.footer{left:0;top:980px;width:1034px;height:185px;background:var(--blue);color:var(--white);font-family:"Arimo",sans-serif;font-size:10.5px}
.footer h4{position:absolute;font-size:10.5px;font-weight:700;padding-bottom:3px;border-bottom:1px dashed rgba(255,255,255,.6)}
.links{position:absolute;left:156px;top:45px;list-style:none;line-height:15.5px}
.contact{position:absolute;left:307px;top:45px;line-height:15px}
.contact div{display:flex;margin-bottom:6px}
.contact b{width:23px;font-weight:700}
.hours{position:absolute;font-size:10px}
.foot-brand{left:528px;top:110px;display:flex;align-items:center;gap:10px}
.foot-brand .brand-square{background:var(--white)}
.foot-brand .brand-name{color:var(--white)}

.bottom{left:0;top:1165px;width:1034px;height:35px;background:var(--black);color:var(--white);font-family:"Arimo",sans-serif;font-size:10px}
.bottom .copy{position:absolute;left:139px;top:12px}
.social{position:absolute;left:495px;top:6px;display:flex;gap:4px}
.social span{height:21px;padding:0 4px;background:#2f5aa8;font-size:8px;line-height:21px;border-radius:2px}
.accept{position:absolute;left:637px;top:12px}
.cards{position:absolute;left:700px;top:6px;display:flex;gap:3px}
.cards span{width:35px;height:22px;background:#3b5ea8;font-size:8px;line-height:22px;text-align:center;border-radius:2px}
</style>
</head>
<body>

<header>
  <div class="abs brand"><span class="brand-square"></span><span class="brand-name">Bluefinch Painting</span></div>
  <div class="abs truck-photo" role="img" aria-label="Company work van with lettering on its side"></div>
  <div class="abs estimate-btn">Free Estimates</div>
  <div class="abs call">
    <svg width="26" height="26" viewBox="0 0 26 26"><circle cx="13" cy="13" r="11.5" fill="none" stroke="#1f7fc4" stroke-width="1.6"/><path d="M9 7c-1 2 0 7 4 10 2 2 4 2 5 1l-2-3-2 1c-2-1-3-3-3-5l2-1-2-3z" fill="#1f7fc4"/></svg>
    <div><small>Call Us Today</small><strong>555-318-7046</strong></div>
  </div>
</header>

<nav class="abs nav">
  <ul>
    <li class="current">Home</li><li>About Us</li><li>Exterior</li><li>Interior</li><li>Residential</li><li>Commerical</li><li>Past Projects</li><li style="border:0">Contact Us</li>
  </ul>
</nav>

<section class="abs hero" role="img" aria-label="Painter applying texture to a yellow wall from a ladder">
  <div class="abs hero-arrow" style="left:98px"><svg width="36" height="36"><path d="M20 11l-7 7 7 7" stroke="#fff" stroke-width="2" fill="none"/></svg></div>
  <div class="abs hero-arrow" style="left:902px"><svg width="36" height="36"><path d="M16 11l7 7-7 7" stroke="#fff" stroke-width="2" fill="none"/></svg></div>
  <p class="abs hero-tag"><em>PROVIDING</em> QUALITY<br>WORK <em>AT</em><br><em>AFFORDABLE PRICES</em></p>
</section>

<section class="abs about">
  <h2>About Bluefinch <span>Painting</span></h2>
  <p>Lorem ipsum dolor sit amet, consectetuer adipiscing elit, sed diam nonummy nibh euismod tincidunt ut laoreet dolore magna aliquam erat volutpat. Ut wisi enim ad minim veniam, quis nostrud exerci tation ullamcorper suscipit lobortis nisl ut aliquip ex ea commodo consequat. Duis autem vel eum iriure dolor in hendrerit in vulputate velit esse molestie consequat, vel illum dolore eu feugiat nulla facilisis at vero eros et accumsan et iusto odio dignissim qui blandit praesent luptatum zzril delenit augue duis dolore ...</p>
  <span class="btn">read more</span>
  <span class="quality">We Proudly Use Quality</span>
  <span class="paint-brand">Ashgrove Paints</span>
</section>

<article class="abs service" style="left:145px">
  <h3>Residential Painting</h3>
  <div class="photo" role="img" aria-label="Freshly painted living room interior" style="background:linear-gradient(90deg,#6b5a4a,#d9d2c6 55%,#1a2340 90%)"></div>
  <p>Sed ut perspiciatis unde omnis iste natus error sit voluptatem accusantium doloremque laudantium, totam rem aperiam.</p>
  <div class="rule"></div><span class="btn">read more</span>
</article>

<article class="abs service" style="left:402px">
  <h3>Commerical Painting</h3>
  <div class="photo" role="img" aria-label="Painter on a ladder rolling paint onto a wall" style="background:linear-gradient(90deg,#e8e5dc,#f5f3ee 80%,#1a2340 88%)"></div>
  <p>Sed ut perspiciatis unde omnis iste natus error sit voluptatem accusantium doloremque laudantium, totam rem aperiam.</p>
  <div class="rule"></div><span class="btn">read more</span>
</article>

<aside class="abs side">
  <h3 class="section-title" style="left:11px;top:24px">Free PAINTING Estimates</h3>
  <div class="form">
    <span class="field">Name</span>
    <span class="field">Email</span>
    <span class="field">Phone</span>
    <span class="field">Address</span>
    <span class="field area">Painting project description</span>
  </div>
  <div class="rule" style="top:282px"></div>
  <span class="submit">Submit</span>
  <span class="gallery-mark"></span>
  <h3 class="section-title" style="left:82px;top:315px">Past Work Gallery</h3>
  <div class="gallery-photo" role="img" aria-label="Past project: painter rolling a white wall">
    <div class="gallery-caption">Lorem Ispum is the Dummy Text</div>
  </div>
  <div class="rule" style="top:529px"></div>
  <div class="gallery-nav"><span></span><span></span></div>
</aside>

<footer class="abs footer">
  <h4 style="left:156px;top:18px;width:82px">Quick Links</h4>
  <ul class="links">
    <li>• Home</li><li>• About Us</li><li>• Exterior</li><li>• Interior</li><li>• Residential</li><li>• Commerical</li><li>• Past Projects</li><li>• Contact Us</li>
  </ul>
  <h4 style="left:307px;top:18px;width:128px">Contact Information</h4>
  <div class="contact">
    <div><b>A:</b><span>Bluefinch Painting<br>Street Name City Name<br>State Zipcode</span></div>
    <div><b>P:</b><span>555-318-7046</span></div>
    <div><b>TF:</b><span>555-318-7046</span></div>
    <div><b>E:</b><span>inquiry@bluefinchpaint.example</span></div>
    <div><b>W:</b><span>bluefinchpainting.example</span></div>
  </div>
  <h4 style="left:525px;top:18px;width:303px">Working Hours</h4>
  <span class="hours" style="left:528px;top:48px">◷ Our work timings are:</span>
  <span class="hours" style="left:702px;top:48px">◷ Saturday:9AM - 4PM</span>
  <span class="hours" style="left:528px;top:72px">◷ Monday - Friday. 8AM - 8PM</span>
  <span class="hours" style="left:702px;top:72px">◷ Sunday: closed</span>
  <div class="abs foot-brand"><span class="brand-square"></span><span class="brand-name">Bluefinch Painting</span></div>
</footer>

<div class="abs bottom">
  <span class="copy">Copyright ©2015, BluefinchPainting  All Rights Reserved</span>
  <div class="social"><span>Kinly</span><span>Chirra</span><span>Plusto</span></div>
  <span class="accept">We Accept</span>
  <div class="cards"><span>Cardo</span><span>Findex</span><span>Vantra</span><span>Amerpay</span><span>Mastro</span></div>
</div>

</body>
</html>
```